Business Cards

Need business card design that I can update for new employees and details. Needs to incorporate our logo, be bright and fun (in line with tourism and holidays)
Would like a Map of Western Australia on the front with locations all the caravan parks we own (just purchased Tom Price so please include that as well as others listed on our website).
Target Market(s)
Famillies
Contact Information for Business Card
5 Cards -
Neil Perrow (Director) e: perrow@wattlebay.com.au p: 0491 570 156
Mira Perrow (Director) e: perrow@wattlebay.com.au p: 0491 570 157
Owen Halvey (General Manager) e: halvey@wattlebay.com.au p: 0491 570 158
Helen Halvey (General Manager) e: halvey@wattlebay.com.au p: 0491 570 159
Colin Danby (Training and Operations Manager) - e: danby@wattlebay.com.au p:0491 570 110
Colors
Look and feel

```html
<!DOCTYPE html>
<html lang="en">
<head>
<meta charset="utf-8">
<title>Wattle Bay Tourist Parks — Business Card</title>
<link rel="stylesheet" href="https://fonts.googleapis.com/css2?family=Cinzel:wght@400&family=Open+Sans:wght@400&display=swap">
<style>
  :root {
    --backdrop: #e9e9e9;
    --card-white: #fbfbfb;
    --teal: #43c3cd;
    --teal-deep: #3bb3bd;
    --ink: #555a5e;
    --ink-soft: #6b7074;
    --brand-grey: #5e6266;
  }
  * { margin: 0; padding: 0; box-sizing: border-box; }
  html, body {
    width: 1200px;
    height: 900px;
    overflow: hidden;
    background: var(--backdrop);
  }
  .stage {
    position: relative;
    width: 1200px;
    height: 900px;
  }
  .card {
    position: absolute;
    top: 297px;
    width: 500px;
    height: 306px;
    border-radius: 2px;
    box-shadow: 0 2px 10px rgba(0,0,0,0.08);
  }
  .card-front {
    left: 70px;
    background: var(--card-white);
    font-family: "Open Sans", sans-serif;
  }
  .card-back {
    left: 630px;
    background: var(--teal);
    display: flex;
    align-items: center;
    justify-content: center;
  }
  .person {
    position: absolute;
    left: 34px;
    top: 34px;
  }
  .person-name {
    font-family: "Cinzel", serif;
    font-weight: 400;
    font-size: 17px;
    letter-spacing: 0.5px;
    color: var(--teal);
    line-height: 1.2;
  }
  .person-role {
    font-size: 11px;
    color: var(--ink);
    margin-top: 1px;
  }
  .contact {
    position: absolute;
    left: 34px;
    top: 108px;
    list-style: none;
  }
  .contact-item {
    display: flex;
    align-items: center;
    gap: 9px;
    font-size: 11.5px;
    color: var(--ink-soft);
    height: 24px;
  }
  .contact-icon {
    width: 11px;
    height: 11px;
    flex: none;
  }
  .brand {
    position: absolute;
    right: 40px;
    bottom: 56px;
    display: flex;
    align-items: center;
    gap: 8px;
  }
  .brand-square {
    width: 30px;
    height: 30px;
    background: var(--teal-deep);
    flex: none;
  }
  .brand-name {
    font-family: "Cinzel", serif;
    font-weight: 400;
    font-size: 15px;
    line-height: 1.15;
    letter-spacing: 1px;
    color: var(--brand-grey);
  }
  .back-wordmark {
    font-family: "Cinzel", serif;
    font-weight: 400;
    font-size: 26px;
    letter-spacing: 2px;
    color: #ffffff;
    text-align: center;
    line-height: 1.25;
  }
</style>
</head>
<body>
<main class="stage">
  <section class="card card-front" aria-label="Business card front">
    <div class="person">
      <h1 class="person-name">NEIL PERROW</h1>
      <p class="person-role">Director</p>
    </div>
    <ul class="contact">
      <li class="contact-item">
        <svg class="contact-icon" viewBox="0 0 12 12" aria-hidden="true">
          <rect width="12" height="12" rx="2" fill="var(--teal)"/>
          <path d="M3.2 2.6 L4.6 2.6 L5.2 4.3 L4.3 5 Q5.1 6.8 7 7.7 L7.7 6.8 L9.4 7.4 L9.4 8.8 Q5.8 9.2 3.2 2.6 Z" fill="#fff"/>
        </svg>
        <span>0491 570 156</span>
      </li>
      <li class="contact-item">
        <svg class="contact-icon" viewBox="0 0 12 12" aria-hidden="true">
          <rect width="12" height="12" rx="2" fill="var(--teal)"/>
          <rect x="2.5" y="3.5" width="7" height="5" fill="none" stroke="#fff" stroke-width="0.9"/>
          <path d="M2.5 3.5 L6 6.4 L9.5 3.5" fill="none" stroke="#fff" stroke-width="0.9"/>
        </svg>
        <span>perrow@wattlebay.com.au</span>
      </li>
    </ul>
    <div class="brand">
      <span class="brand-square" aria-hidden="true"></span>
      <span class="brand-name">Wattle Bay<br>Tourist Parks</span>
    </div>
  </section>

  <section class="card card-back" role="img" aria-label="Card back: brand artwork on teal with the Wattle Bay Tourist Parks name">
    <p class="back-wordmark">Wattle Bay<br>Tourist Parks</p>
  </section>
</main>
</body>
</html>
```